Fitness Equipment & Service

I want to make the card eye catching and fun. We are called Corvane Motion Limited and we are based in Wales. We sell, install and service all types of fitness equipment from Skipping ropes, right through the Dumbbells, Kettle bells and Barbells through to state of the art Treadmills, Running Machines and Strength Equipment. We also design and install changing room furniture and lockers.

TYPOGRAPHY
We would like to use Futrura. Futura has an appearance of efficiency and forwardness. The typeface is derived
from simple geometric forms (near-perfect circles, triangles and squares) and is based on strokes of
near-even weight, which are low in contrast. This is most visible in the almost perfectly round stroke of
the o, which is nonetheless slightly ovoid.
The lowercase has tall ascenders, which rise above the cap line. The uppercase
characters present proportions similar to those of classical Roman capitals.

TYPOGRAPHIC CONSIDERATIONS
No Strike though
No Horizontal Scaling
No Drop Shadows
No Effects
Never use less than 120% Leading

OUR CORPORATE COLOURS
BRAND GUIDELINES
We were thinking that our primary colour palette consists of the Acid Green (Pantone 382) and Process Black.

We work closely with tquarly Ltd and would like to include their name on the card somewhere. I have attached images of the other brands that we work with as an idea or the small icons I have included that illustrate what we do?. I have very kindly been given permission to use any of the images off the files that I have included below, so I hope these help. I will include these below. I would be open to suggestions if it made the card more striking Can you do it?
Updates

Hi All, Just wanted to add a few thoughts but you are the guys with the creative visions (thats why are here) We are based in Wales, UK and we would be open to lots of different ideas on a theme but must be eye catching, Bold and FUN. If you can or think that the Welsh or any dragon could be put in there then go for it (its not a must have) We have also added some ideas for colour but again its over to you!! GO FOR IT ! Thanks and look forward to your visions! Owen

Hi All, Just thought I would sen through the contact details that need to be on the card. (if you want to play around with icons instead of the wording twitter, Facebook, go for it): Corvane Motion Limited Owen Pritchard Managing Director Mob: +44 (0)7582 913 406 e-mail: sales@corvanemotion.co.uk Web: Corvanemotion.co.uk twitter: @motionLetterbin Facebook: Corvane Motion Limited

```html
<!DOCTYPE html>
<html lang="en">
<head>
<meta charset="utf-8">
<title>Corvane Motion Limited – Business Card</title>
<link href="https://fonts.googleapis.com/css2?family=Jost:wght@400;500;700&display=swap" rel="stylesheet">
<style>
  :root {
    --page: #e6e5e1;
    --card: #ffffff;
    --card-edge: #d6d6d6;
    --acid: #c4d600;
    --acid-deep: #8fa000;
    --black: #111111;
    --ink: #2a2a2a;
    --muted: #8a8a8a;
  }
  html, body {
    margin: 0;
    width: 1200px;
    height: 892px;
    overflow: hidden;
    background: var(--page);
    font-family: "Jost", "Futura", sans-serif;
  }
  .sheet { position: relative; width: 1200px; height: 892px; }
  .card {
    position: absolute;
    top: 292px;
    width: 540px;
    height: 308px;
    border-radius: 16px;
    box-shadow: 0 2px 0 var(--card-edge), 0 12px 32px rgba(0,0,0,.16);
    overflow: hidden;
  }
  .card--front { left: 40px; background: var(--card); }
  .card--back  { left: 620px; background: var(--black); }

  /* front */
  .card--front::before {
    content: "";
    position: absolute;
    left: 0; top: 0; bottom: 0;
    width: 10px;
    background: var(--acid);
  }
  .holder { position: absolute; left: 36px; top: 28px; }
  .holder__name {
    margin: 0;
    font-size: 30px;
    font-weight: 700;
    color: var(--black);
    line-height: 1.2;
  }
  .holder__role {
    margin: 0;
    font-size: 17px;
    font-weight: 500;
    color: var(--acid-deep);
    line-height: 1.3;
  }
  .divider {
    position: absolute;
    left: 36px; top: 118px;
    width: 290px; height: 3px;
    background: var(--acid);
  }
  .contacts {
    position: absolute;
    left: 36px; top: 134px;
    margin: 0; padding: 0;
    list-style: none;
  }
  .contacts li {
    display: flex;
    align-items: center;
    gap: 12px;
    font-size: 15px;
    color: var(--ink);
    line-height: 1.45;
  }
  .contacts svg { width: 14px; height: 14px; flex: none; }
  .social {
    position: absolute;
    left: 36px; right: 30px; bottom: 24px;
    display: flex;
    justify-content: space-between;
    font-size: 17px;
    color: var(--ink);
    line-height: 1.3;
  }
  .social__item { display: flex; align-items: center; gap: 10px; }
  .social__mark {
    width: 20px; height: 20px;
    background: var(--acid);
    border-radius: 3px;
  }
  .brand { position: absolute; display: flex; align-items: center; gap: 14px; }
  .brand--front { right: 30px; top: 32px; }
  .brand__dot { border-radius: 50%; background: var(--acid); flex: none; }
  .brand--front .brand__dot { width: 62px; height: 62px; }
  .brand__name {
    margin: 0;
    font-weight: 700;
    text-transform: uppercase;
    line-height: 1.2;
  }
  .brand--front .brand__name { font-size: 13px; width: 90px; color: var(--black); }

  /* back */
  .brand--back {
    left: 50%; top: 46%;
    transform: translate(-50%, -50%);
    gap: 22px;
  }
  .brand--back .brand__dot { width: 150px; height: 150px; }
  .brand--back .brand__name { font-size: 22px; width: 160px; color: var(--acid); }
  .partner {
    position: absolute;
    left: 0; right: 0; bottom: 22px;
    margin: 0;
    text-align: center;
    font-size: 14px;
    color: #ffffff;
    line-height: 1.3;
    letter-spacing: .04em;
  }
</style>
</head>
<body>
<main class="sheet">
  <section class="card card--front" aria-label="Card front">
    <div class="holder">
      <h1 class="holder__name">Owen Pritchard</h1>
      <p class="holder__role">Managing Director</p>
    </div>
    <div class="divider"></div>
    <ul class="contacts">
      <li>
        <svg viewBox="0 0 13 13" aria-hidden="true"><rect x="3" y="0.5" width="7" height="12" rx="1.5" fill="none" stroke="#8fa000" stroke-width="1.4"/><circle cx="6.5" cy="10.3" r=".9" fill="#8fa000"/></svg>
        +44 (0)7582 913 406
      </li>
      <li>
        <svg viewBox="0 0 13 13" aria-hidden="true"><rect x=".7" y="2.5" width="11.6" height="8" fill="none" stroke="#8fa000" stroke-width="1.4"/><path d="M1 3 L6.5 7.5 L12 3" fill="none" stroke="#8fa000" stroke-width="1.4"/></svg>
        sales@corvanemotion.co.uk
      </li>
      <li>
        <svg viewBox="0 0 13 13" aria-hidden="true"><circle cx="6.5" cy="6.5" r="5.8" fill="none" stroke="#8fa000" stroke-width="1.3"/><ellipse cx="6.5" cy="6.5" rx="2.5" ry="5.8" fill="none" stroke="#8fa000" stroke-width="1.1"/><path d="M.8 6.5 H12.2" stroke="#8fa000" stroke-width="1.1"/></svg>
        Corvanemotion.co.uk
      </li>
    </ul>
    <div class="social">
      <span class="social__item"><span class="social__mark"></span>@motionLetterbin</span>
      <span class="social__item"><span class="social__mark"></span>Corvane Motion Limited</span>
    </div>
    <div class="brand brand--front">
      <span class="brand__dot"></span>
      <p class="brand__name">Corvane Motion Limited</p>
    </div>
  </section>

  <section class="card card--back" aria-label="Card back">
    <div class="brand brand--back">
      <span class="brand__dot"></span>
      <p class="brand__name">Corvane Motion Limited</p>
    </div>
    <p class="partner">In partnership with tquarly Ltd</p>
  </section>
</main>
</body>
</html>
```